PillPeak website blog. Simple medical advice given in clear yes or no answers that save people money

I am developing a new web page that provides medical care cost savings at the consumers' fingertips. I need a web page that is clean, concise, and attractive for me to put my valuable medical information on. The information I provide is simple to obtain, yet very valuable to the consumer, and answered in a yes or no format. For example, A person may wonder if they need an antibiotic for cold like symptoms. Seeing a doctor for an antibiotic is very expensive. But with simple and clear advice at their fingertips, they can confidently avoid having to pay $200 or more to see a doctor and get an antibiotic. This is kind of like consumer reports for medical services.

Target Market(s)

People who are savvy shoppers and want to save money on healthcare. Likely younger ages between 21 and 60, who are mobile, readily use iphones, and want strong evidence based research to guide their decisions.

Industry/Entity Type

Coding

Number of Pages Required

Colors

Requirements
Must have
• A template on the "Question" and "Answer" page that can be edited many times that can be edited many times. The Confidence rating scale would need to be edited as well. The "Date Researched" the "PillPeak Pilluminate" and "References" all need to be able to be edited. This website must be very clear and simple to understand. A medical question is posed with a yes or no answer, then answered and given a confidence rating, we then tell them how much money they saved by going to our website.
Nice to have
• We want this to be slightly fun, vibrant, warm and inviting. This will be sometime later converted into an app format. Quirky, some humor to keep it interesting.
Should not have
• No sterile looking medical images. Not boring.

```html
<!DOCTYPE html>
<html lang="en">
<head>
<meta charset="utf-8">
<title>PillPeak — Clear. Valuable. Health. Advice.</title>
<link rel="stylesheet" href="https://fonts.googleapis.com/css2?family=Roboto:wght@400;500;700&family=Roboto+Condensed:wght@400;500&family=Bebas+Neue&display=swap">
<style>
  :root {
    --red: #e32b3c;
    --red-deep: #e0111f;
    --blue: #1a7ad8;
    --blue-dark: #1664bb;
    --ink: #1e1e1e;
    --hero-bg: #dfe0e4;
    --footer-bg: #1f1f1f;
    --white: #ffffff;
    --search-bg: #ececec;
    --teal-dark: #0d3c4a;
    --teal: #1aa7c4;
  }
  * { box-sizing: border-box; margin: 0; padding: 0; }
  html, body { width: 1200px; height: 946px; overflow: hidden; }
  body { font-family: "Roboto", sans-serif; background: var(--white); position: relative; color: var(--ink); }

  .site-header { position: absolute; left: 0; top: 0; width: 1200px; height: 147px; background: var(--white); }
  .brand { position: absolute; left: 143px; top: 48px; display: flex; align-items: center; gap: 10px; }
  .brand-dot { width: 40px; height: 40px; border-radius: 50%; background: var(--blue); }
  .brand-name { font-family: "Roboto", sans-serif; font-weight: 700; font-size: 34px; color: var(--red-deep); letter-spacing: -0.5px; }

  .search { position: absolute; left: 804px; top: 27px; width: 251px; height: 35px; border-radius: 18px; background: var(--search-bg); display: flex; align-items: center; padding: 0 14px; font-size: 13px; color: #666; justify-content: space-between; }
  .tagline { position: absolute; right: 145px; top: 82px; font-size: 29px; font-weight: 500; color: var(--ink); letter-spacing: 0.2px; white-space: nowrap; }

  .main-nav { position: absolute; left: 0; top: 147px; width: 1200px; height: 51px; background: var(--red); display: flex; justify-content: center; padding-left: 20px; }
  .main-nav a { font-family: "Roboto Condensed", sans-serif; font-size: 16.5px; color: var(--white); text-decoration: none; line-height: 51px; padding: 0 19px; border-right: 1px solid rgba(0,0,0,0.12); }
  .main-nav a:last-child { border-right: none; }

  .hero { position: absolute; left: 0; top: 198px; width: 1200px; height: 562px; background: var(--hero-bg); overflow: hidden; }
  .hero-art { position: absolute; left: 780px; top: 0; width: 420px; height: 562px;
    background: linear-gradient(100deg, var(--hero-bg) 0%, #9fcfdc 40%, var(--teal) 75%, #117fa3 100%); }
  .side-menu { position: absolute; left: 0; top: 67px; width: 281px; }
  .side-menu a { display: block; height: 58.4px; line-height: 58.4px; padding-left: 26px; font-weight: 700; font-size: 17px; color: var(--white); text-decoration: none; background: var(--blue); }
  .side-menu a:nth-child(even) { background: var(--blue-dark); }

  .headline { position: absolute; left: 330px; top: 172px; font-family: "Bebas Neue", sans-serif; font-weight: 400; font-size: 53px; line-height: 61px; letter-spacing: -1.5px; color: var(--ink); white-space: nowrap; }
  .headline .accent { color: var(--red-deep); display: block; }
  .slide-next { position: absolute; left: 1121px; top: 311px; width: 34px; height: 34px; border-radius: 50%; background: var(--teal-dark); display: flex; align-items: center; justify-content: center; }

  .site-footer { position: absolute; left: 0; top: 760px; width: 1200px; height: 186px; background: var(--footer-bg); color: var(--white); }
  .disclaimer { position: absolute; left: 143px; top: 35px; font-size: 15px; }
  .copyright { position: absolute; left: 143px; top: 72px; font-size: 15.5px; }
  .social { position: absolute; left: 143px; top: 112px; display: flex; gap: 8px; }
  .social span { width: 28px; height: 28px; border-radius: 50%; border: 2px solid var(--white); }
  .join-title { position: absolute; left: 669px; top: 35px; font-size: 20.5px; font-weight: 500; }
  .signup { position: absolute; left: 670px; top: 76px; display: flex; gap: 12px; }
  .signup .email { width: 259px; height: 40px; background: var(--white); color: #444; font-size: 11px; padding-left: 13px; line-height: 40px; }
  .signup .subscribe { width: 114px; height: 38px; background: var(--red-deep); font-weight: 500; font-size: 15px; line-height: 38px; text-align: center; margin-top: 1px; }
  .ask { position: absolute; left: 670px; top: 130px; font-family: "Roboto Condensed", sans-serif; font-size: 16px; }
</style>
</head>
<body>
  <header class="site-header">
    <div class="brand"><span class="brand-dot"></span><span class="brand-name">PillPeak</span></div>
    <div class="search">Search
      <svg width="12" height="12" viewBox="0 0 12 12"><circle cx="5" cy="5" r="3.8" fill="none" stroke="#555" stroke-width="1.8"/><line x1="8" y1="8" x2="11" y2="11" stroke="#555" stroke-width="1.8"/></svg>
    </div>
    <div class="tagline">CLEAR. VALUABLE. HEALTH. ADVICE. RIGHT NOW</div>
  </header>

  <nav class="main-nav">
    <a href="#">PREV/SCREENING</a><a href="#">WOMEN'S HEALTH</a><a href="#">MEN'HEALTH</a><a href="#">MEDS</a><a href="#">SURGERY</a><a href="#">IMAGERY</a><a href="#">PEDS</a><a href="#">CONTACT</a>
  </nav>

  <section class="hero">
    <div class="hero-art" role="img" aria-label="Illustration of glossy blue molecules joined by grey rods"></div>
    <nav class="side-menu">
      <a href="#">WHO WE ARE ?</a><a href="#">HOW IT WORKS</a><a href="#">HOW WE KNOW</a><a href="#">EVIDENCE BASED RESEARCH</a><a href="#">DR.HOLLOWAY</a><a href="#">WHO WE ARE NOT</a><a href="#">ARE WE BIASED?</a>
    </nav>
    <h1 class="headline">DON'T SPEND ANOTHER CLINIC<span class="accent">ON YOUR HEALTH BEFORE</span>CHECKING US OUT ! IT'S FREE</h1>
    <div class="slide-next"><svg width="12" height="16" viewBox="0 0 12 16"><polyline points="3,2 9,8 3,14" fill="none" stroke="#fff" stroke-width="2.4"/></svg></div>
  </section>

  <footer class="site-footer">
    <div class="disclaimer">DISCLAIMER</div>
    <div class="copyright">Copyright © 2018.PillPeak. All rights reserved.</div>
    <div class="social"><span aria-label="Social link"></span><span aria-label="Social link"></span><span aria-label="Social link"></span></div>
    <div class="join-title">BECOME A PILLPEAK TODAY!</div>
    <div class="signup"><div class="email">Enter email</div><div class="subscribe">SUBSCRIBE</div></div>
    <div class="ask">Ask a Question Here! If it is Worthy,Will post it!</div>
  </footer>
</body>
</html>
```